Velvet Moon Wheel Method Needs a Website

I require a Wordpress website so that I can do simple edits myself. I want it to be a fairly simple design as the videos and the text will speak for themselves.
The concept is simple, we have developed a revolutionary roulette system that proves the game is NOT random. This breakthrough is absolutely massive. We are offering a 12-part training course to take a beginner to a professional at their own pace through watching videos made by our roulette genius.
Roulette and casinos have a glitzy feel about them and this should be reflected in the style of the site. The roulette wheel, table and chips are very evocative and pictures of these would be good.
There is a home page and 5 other pages containing sub-pages. These should be interlinked and it must be easy to get back to the home page from anywhere on the site.
Coinvey links should appear at the bottom of each page.
I really need the site in a hurry as we were let down badly by the last developer we hired who went on holiday and left us in the lurch.

Target Market(s)

Gamblers, betting community, opportunity seekers

Coding

Coded - Design and coding required

Number of Pages Required

1 page

Font styles to use
Sans Serif

Requirements
Must have
• At least two videos on the Home page.
• Coinvey details on every page and tab.
• A box for name and email address for interested parties to leave their details.

```html
<!DOCTYPE html>
<html lang="en">
<head>
<meta charset="utf-8">
<title>Velvet Moon Wheel Method</title>
<link href="https://fonts.googleapis.com/css2?family=Open+Sans:wght@300;400;600;700;800&display=swap" rel="stylesheet">
<style>
:root{
  --orange:#e8541e;
  --slate:#3e4450;
  --slate-dark:#2b2f38;
  --charcoal:#2d2d2d;
  --panel:#474747;
  --light:#ebebeb;
  --white:#ffffff;
  --ink:#333333;
  --muted:#b9bcc3;
}
*{box-sizing:border-box;margin:0;padding:0}
html,body{width:1200px;height:3169px;overflow:hidden}
body{font-family:"Open Sans",Arial,sans-serif;color:var(--ink);background:var(--white)}
.section{position:relative;width:1200px;overflow:hidden}
.abs{position:absolute}
.btn{position:absolute;background:var(--orange);color:var(--white);font-weight:700;text-transform:uppercase;display:flex;align-items:center;justify-content:center;gap:10px}

/* top bar */
.topbar{height:30px;background:var(--slate);color:#dfe2e7;font-size:11px}
.topbar .items{position:absolute;right:133px;top:0;height:30px;display:flex;align-items:center;gap:18px}
.topbar .social{display:flex;gap:7px;align-items:center}
.topbar .social span{width:12px;height:12px;border-radius:50%;background:#dfe2e7;display:block}

/* header */
.header{height:110px;background:var(--white)}
.logo-mark{left:222px;top:6px;width:52px;height:52px;border-radius:50%;background:var(--slate)}
.logo-name{left:130px;top:66px;font-size:19px;font-weight:700;color:var(--orange);letter-spacing:.2px;white-space:nowrap}
.search{left:808px;top:18px;width:122px;height:34px;border:1px solid #cfd2d6;font-size:10px;display:flex;align-items:center;padding-left:10px;gap:8px;color:#555;font-weight:600}
.cart{left:945px;top:18px;width:122px;height:34px;background:var(--slate);color:var(--white);font-size:10px;font-weight:700;display:flex;align-items:center;justify-content:center;gap:8px}
.nav{right:133px;top:68px;display:flex;gap:4px;font-size:13.5px;color:var(--ink)}
.nav a{padding:5px 12px;color:inherit;text-decoration:none}
.nav a.active{background:var(--orange);color:var(--white);font-weight:700}

/* hero */
.hero{height:456px;background:radial-gradient(circle at 72% 45%,#c9a24a 0,#8a6a2a 18%,#5a2a1e 36%,#1d1b1c 62%,#101010 100%)}
.hero h1{left:130px;top:122px;color:var(--white);font-size:41px;font-weight:800;line-height:57px;letter-spacing:.5px}
.hero .btn{left:130px;top:265px;width:146px;height:45px;font-size:15px}
.hero .arrow{top:195px;width:38px;height:66px;background:rgba(255,255,255,.55)}
.hero .arrow.left{left:0;border-radius:0 33px 33px 0}
.hero .arrow.right{right:0;border-radius:33px 0 0 33px}
.dots{left:540px;top:430px;display:flex;gap:17px}
.dots span{width:11px;height:11px;border-radius:50%;background:var(--white)}
.dots span.on{background:transparent;border:2px solid var(--white)}

/* welcome */
.welcome{height:422px}
.welcome .eyebrow{left:130px;top:58px;font-size:15px;font-weight:700}
.welcome .title{left:130px;top:82px;font-size:26px;font-weight:700;color:var(--orange);white-space:nowrap}
.welcome .lead{left:130px;top:132px;width:440px;font-size:12.5px;font-weight:700;line-height:19px}
.welcome .body{left:130px;top:180px;width:440px;font-size:12.5px;line-height:19px;color:#444}
.welcome .btn{left:130px;top:294px;width:219px;height:45px;font-size:15px}
.video{left:594px;top:44px;width:473px;height:318px;background:linear-gradient(160deg,#e6e3dd 0,#8a8478 28%,#1f6b55 55%,#0f4a3a 100%)}
.play{position:absolute;width:80px;height:80px;border-radius:50%;border:5px solid var(--white);background:rgba(255,255,255,.25)}
.play::after{content:"";position:absolute;left:28px;top:19px;border-left:26px solid var(--white);border-top:16px solid transparent;border-bottom:16px solid transparent}
.video .play{left:197px;top:110px}
.vbar{position:absolute;left:0;bottom:0;height:20px;background:#1c1c1c;display:flex;align-items:center;gap:10px;padding:0 8px;color:#ccc;font-size:9px}
.video .vbar{width:473px}
.track{flex:1;height:4px;background:#555;position:relative}
.track i{position:absolute;left:0;top:0;width:15%;height:4px;background:#ddd}

/* section badge + title */
.badge{left:576px;width:48px;height:48px;border-radius:50%;border:3px solid var(--white);background:var(--slate);display:flex;align-items:center;justify-content:center}
.sec-title{left:0;width:1200px;text-align:center;font-size:31px;font-weight:700;color:var(--orange)}
.sec-title::after{content:"";display:block;width:152px;height:2px;background:var(--orange);margin:6px auto 0}

/* training */
.training{height:383px;background:radial-gradient(circle at 50% 65%,#4d525e 0,var(--slate) 60%)}
.cards{left:130px;top:122px;display:flex;gap:6px}
.card{width:231px;height:165px;background:var(--slate-dark);border:1px solid #555b66;text-align:center;color:var(--white);padding-top:22px}
.card svg{width:52px;height:52px;stroke:var(--orange);fill:none;stroke-width:2.4}
.card h3{font-size:12.5px;font-weight:700;margin-top:12px;line-height:16px;height:34px;display:flex;align-items:center;justify-content:center;text-transform:uppercase}
.card p{font-size:10.5px;color:var(--muted);line-height:14px;padding:0 18px;margin-top:2px}

/* casino */
.casino{height:511px;background:var(--charcoal)}
.tab{left:130px;width:248px;height:52px;border:2px solid #6a6a6a;color:var(--white);font-size:13.5px;display:flex;align-items:center;padding-left:20px;gap:18px}
.tab.active{background:var(--orange);border-color:var(--orange);width:238px}
.tab.active::after{content:"";position:absolute;right:-14px;top:10px;border-left:14px solid var(--orange);border-top:14px solid transparent;border-bottom:14px solid transparent}
.tab .ic{width:18px;height:18px;border-radius:50%;border:2px solid var(--white)}
.casino-panel{left:400px;top:133px;width:667px;height:329px;background:var(--panel);box-shadow:0 4px 10px rgba(0,0,0,.5)}
.casino-video{left:0;top:0;width:355px;height:329px;background:radial-gradient(circle at 55% 70%,#c93c26 0,#6e2a1d 30%,#4b4037 55%,#3a3a3a 100%)}
.casino-video .play{left:137px;top:115px}
.casino-video .vbar{width:355px}
.casino-panel h3{left:375px;top:28px;font-size:21px;font-weight:700;color:var(--orange)}
.casino-panel p{left:375px;width:270px;font-size:11px;line-height:17px;color:#e3e3e3;text-align:justify}
.casino-panel .btn{left:375px;top:280px;width:92px;height:26px;font-size:10.5px}

/* plan */
.plan{height:454px;background:linear-gradient(180deg,#e4e4e4,#efefef)}
.price-card{top:138px;width:346px;height:264px;background:var(--white);box-shadow:0 2px 8px rgba(0,0,0,.12);text-align:center}
.price-card h3{margin-top:28px;font-size:24px;font-weight:400;color:#222}
.price-box{position:absolute;left:36px;top:80px;width:274px;height:152px;border:2px solid #d4d4d4;padding-top:18px}
.price{font-size:62px;font-weight:300;color:var(--orange);line-height:72px}
.price small{font-size:16px;font-weight:400}
.price-note{font-size:17px;font-weight:600;letter-spacing:3px;color:#444;margin-top:10px}

/* vegas */
.vegas{height:353px;background:linear-gradient(180deg,#f4efe6 0,#ece6dc 50%,#dfe0de 100%)}
.vegas-box{left:193px;top:44px;width:814px;height:233px;border:2px solid #d7d7d7;background:rgba(255,255,255,.72);text-align:center}
.vegas-box h2{margin-top:42px;font-size:30px;font-weight:700;color:var(--orange)}
.vegas-box p{width:720px;margin:14px auto 0;font-size:13.5px;line-height:22px;color:#333}

/* footer */
.footer{height:450px;background:var(--slate);color:var(--white)}
.f-mark{left:222px;top:52px;width:60px;height:60px;border-radius:50%;background:#dfe2e7}
.f-name{left:110px;top:126px;width:284px;text-align:center;font-size:14.5px;font-weight:600;white-space:nowrap}
.f-follow{left:130px;top:178px;width:244px;text-align:center;font-size:10px;font-weight:700}
.f-social{left:186px;top:200px;display:flex;gap:12px}
.f-social span{width:26px;height:26px;border-radius:50%;background:#5b6270}
.f-col h4{font-size:12px;font-weight:700;margin-bottom:18px}
.f-col p,.f-col li{font-size:11px;line-height:24px;color:#dcdfe4;list-style:none}
.field{left:772px;width:295px;height:36px;background:#5a606c;font-size:11px;display:flex;align-items:center;padding-left:14px;gap:14px;color:#e0e0e0}
.field i{width:10px;height:10px;background:#e0e0e0;display:block}
.signup{left:772px;top:212px;width:295px;height:46px;font-size:19px}
.f-rule{left:130px;top:310px;width:937px;height:1px;background:#5d6470}
.copy{left:130px;top:366px;font-size:10.5px;color:#dcdfe4}
.pay{left:822px;top:343px;width:245px;height:64px;border:2px solid #c8ccd2;border-radius:4px;padding:4px 10px}
.pay .pay-name{font-size:12px;font-weight:700;color:#dfe6f2}
.pay .cards-row{display:flex;gap:6px;margin-top:4px}
.pay .cards-row span{width:50px;height:28px;background:#eef0f3;color:var(--slate);font-size:9px;font-weight:700;display:flex;align-items:center;justify-content:center}
</style>
</head>
<body>

<header>
  <div class="section topbar">
    <div class="items">
      <span>&#9742;&nbsp; 020 7946 0183</span>
      <span>&#9993;&nbsp; hello@velvetmoon.example</span>
      <span class="social">Follow us : <span></span><span></span><span></span><span></span></span>
    </div>
  </div>
  <div class="section header">
    <div class="abs logo-mark"></div>
    <div class="abs logo-name">VELVET MOON WHEEL METHOD</div>
    <div class="abs search">&#9906; SEARCH</div>
    <div class="abs cart">&#128722; MY CART &nbsp;$0.00</div>
    <nav class="abs nav">
      <a class="active" href="#">Home</a><a href="#">Training</a><a href="#">Casinos</a><a href="#">Coaching</a><a href="#">Overseas Trip</a><a href="#">FAQ</a><a href="#">Contact Us</a>
    </nav>
  </div>
</header>

<section class="section hero" role="img" aria-label="Close-up photo of a spinning roulette wheel with a gold turret">
  <div class="abs arrow left"></div>
  <div class="abs arrow right"></div>
  <h1 class="abs">REVOLUTIONARY<br>ROULETTE SYSTEM</h1>
  <div class="btn">Learn More</div>
  <div class="abs dots"><span></span><span class="on"></span><span></span><span></span><span></span></div>
</section>

<section class="section welcome">
  <div class="abs eyebrow">WELCOME TO</div>
  <div class="abs title">VELVET MOON WHEEL METHOD</div>
  <p class="abs lead">Lorem ipsum dolor sit amet, consectetur adipiscing elit, sed do eiusmod tempor incididunt ut labore et dolore</p>
  <p class="abs body">But I must explain to you how all this mistaken idea of denouncing pleasure and praising pain was born and I will give you a complete account of the system, and expound the actual teachings of the great explorer of the truth, the master-builder of human happiness. No one rejects, dislikes, or avoids pleasure itself,</p>
  <div class="btn">&#9654; Watch This Video</div>
  <div class="abs video" role="img" aria-label="Video still of a dealer's hands above a green casino table with chips">
    <div class="play"></div>
    <div class="vbar">&#9654;<span class="track"><i></i></span>1:30 / 4:20 &#9834; &#9881;</div>
  </div>
</section>

<section class="section training">
  <div class="abs badge" style="top:-18px"></div>
  <h2 class="abs sec-title" style="top:42px">TRAINING</h2>
  <div class="abs cards">
    <div class="card">
      <svg viewBox="0 0 56 56"><rect x="12" y="8" width="32" height="42" rx="2"/><rect x="21" y="4" width="14" height="8"/><line x1="19" y1="22" x2="37" y2="22"/><line x1="19" y1="30" x2="37" y2="30"/><line x1="19" y1="38" x2="31" y2="38"/></svg>
      <h3>Course Description</h3>
      <p>At vero eos et accusamus et iusto odio dignissimos ducimus qui blanditiis praesentium.</p>
    </div>
    <div class="card">
      <svg viewBox="0 0 56 56"><rect x="8" y="14" width="40" height="32" rx="2"/><rect x="23" y="8" width="10" height="9"/><circle cx="20" cy="27" r="4"/><path d="M13 38c2-5 12-5 14 0"/><line x1="32" y1="26" x2="42" y2="26"/><line x1="32" y1="33" x2="42" y2="33"/></svg>
      <h3>Monthly Membership</h3>
      <p>At vero eos et accusamus et iusto odio dignissimos ducimus qui blanditiis praesentium.</p>
    </div>
    <div class="card">
      <svg viewBox="0 0 56 56"><circle cx="28" cy="28" r="9"/><path d="M28 6v7M28 43v7M6 28h7M43 28h7M12 12l5 5M39 39l5 5M44 12l-5 5M17 39l-5 5"/><circle cx="28" cy="28" r="16"/></svg>
      <h3>The Complete System</h3>
      <p>At vero eos et accusamus et iusto odio dignissimos ducimus qui blanditiis praesentium.</p>
    </div>
    <div class="card">
      <svg viewBox="0 0 56 56"><path d="M20 36c-4-3-6-7-6-11a14 14 0 0 1 28 0c0 4-2 8-6 11v5H20z"/><line x1="22" y1="46" x2="34" y2="46"/><path d="M28 2v5M8 10l4 3M48 10l-4 3M3 26h5M48 26h5"/></svg>
      <h3>Intellectual<br>Property Rights</h3>
      <p>At vero eos et accusamus et iusto odio dignissimos ducimus qui blanditiis praesentium.</p>
    </div>
  </div>
</section>

<section class="section casino">
  <div class="abs badge" style="top:-18px;background:var(--charcoal)"></div>
  <h2 class="abs sec-title" style="top:52px">CASINO</h2>
  <div class="abs tab active" style="top:137px"><span class="ic"></span>Reputable Casinos</div>
  <div class="abs tab" style="top:214px"><span class="ic" style="border-radius:2px"></span>Casino Bonuses</div>
  <div class="abs tab" style="top:293px"><span class="ic"></span>RNG vs Real Wheel</div>
  <div class="abs casino-panel">
    <div class="abs casino-video" role="img" aria-label="Video still of a roulette wheel with a white ball in a red pocket">
      <div class="play"></div>
      <div class="vbar">&#9654;<span class="track"><i></i></span>0:45 / 3:10 &#9834; &#9881;</div>
    </div>
    <h3 class="abs">Reputable Casinos</h3>
    <p class="abs" style="top:68px">On the other hand, we denounce with righteous indignation and dislike men who are so beguiled and demoralized by the charms of pleasure of the moment.</p>
    <p class="abs" style="top:152px">In a free hour, when our power of choice is untrammelled and when nothing prevents our being able to do what we like best, every pleasure is to be welcomed and every pain avoided. But in certain circumstances and owing to the claims of duty or the obligations .</p>
    <div class="btn">Read More</div>
  </div>
</section>

<section class="section plan">
  <div class="abs badge" style="top:-18px;background:var(--slate)"></div>
  <h2 class="abs sec-title" style="top:46px">OUR PLAN</h2>
  <div class="abs price-card" style="left:233px">
    <h3>Monthly Subscription</h3>
    <div class="price-box"><div class="price">£100.00<small>GBP</small></div><div class="price-note">FOR EACH MONTH</div></div>
  </div>
  <div class="abs price-card" style="left:633px">
    <h3>Single Payment</h3>
    <div class="price-box"><div class="price">£100.00<small>GBP</small></div><div class="price-note">ONE TIME PAYMENT</div></div>
  </div>
</section>

<section class="section vegas" role="img" aria-label="Hazy photo of a city skyline at dusk">
  <div class="abs vegas-box">
    <h2>LAS VEGAS</h2>
    <p>On the other hand, we denounce with righteous indignation and dislike men who are so beguiled and demoralized by the charms of pleasure of the moment. so blinded by desire. that they cannot foresee the pain and trouble that are bound to ensue. and equal blame belongs.</p>
  </div>
</section>

<footer class="section footer">
  <div class="abs f-mark"></div>
  <div class="abs f-name">VELVET MOON WHEEL METHOD</div>
  <div class="abs f-follow">FOLLOW US ON</div>
  <div class="abs f-social"><span></span><span></span><span></span><span></span></div>

  <div class="abs f-col" style="left:452px;top:48px">
    <h4>CONTACT US</h4>
    <p>27 Larkspur Row<br>Brightwell, BW4 7QT<br>T : 0.800.555.0142<br>E : info@velvetmoon.example</p>
  </div>
  <div class="abs f-col" style="left:640px;top:48px">
    <h4>MENU</h4>
    <ul><li>Home</li><li>Training</li><li>Casinos</li><li>Coaching</li><li>Overseas Trip</li><li>FAQ</li><li>Contact</li></ul>
  </div>
  <div class="abs f-col" style="left:772px;top:48px">
    <h4 style="margin-bottom:4px">NEWSLETTER SIGNUP!</h4>
    <p>Get more details to signup!</p>
  </div>
  <div class="abs field" style="top:110px"><i></i>Name</div>
  <div class="abs field" style="top:160px"><i></i>E mail id</div>
  <div class="btn signup">Signup!</div>

  <div class="abs f-rule"></div>
  <div class="abs copy">Copyrights @ 2016 All Rights Reserved</div>
  <div class="abs pay">
    <div class="pay-name">Coinvey</div>
    <div class="cards-row"><span>Nova</span><span>Meridian</span><span>Orbis</span><span>Crestline</span></div>
  </div>
</footer>

</body>
</html>
```